RWT Fittings Ltd Business Cards

We need a business card with our business logo. We provide window and door installations on high-rises in west coast British Colombia, Canada.

I would like my business information and details on one side of the card, and the other side the company name with logo

Target Market(s)

General Contractors

Industry/Entity Type

Construction

Contact Information for Business Card

one side i want my company name and logo in the dark theme logo that i provided

Requirements
Must have
• Marco Peltieri, 16045518293, RWTFittings@mailbox-demo.com, 1407-5194 Linden Row Burnaby BC, V5H 2K9, Owner & Manager

```html
<!DOCTYPE html>
<html lang="en">
<head>
<meta charset="utf-8">
<title>RWT Fittings Ltd Business Cards</title>
<link href="https://fonts.googleapis.com/css2?family=Roboto:wght@400;500;700&family=Roboto+Condensed:wght@700&display=swap" rel="stylesheet">
<style>
  :root {
    --stage: #232323;
    --card-dark: #1f1f22;
    --brand-blue: #29abe2;
    --text-light: #f2f2f2;
    --text-grey: #9a9a9a;
    --ink: #141416;
  }
  * { box-sizing: border-box; margin: 0; padding: 0; }
  html, body { width: 1200px; height: 780px; overflow: hidden; background: var(--stage); }
  .canvas {
    position: relative; width: 1200px; height: 780px;
    display: flex; align-items: center; justify-content: center; gap: 40px;
    font-family: "Roboto", Arial, sans-serif;
  }
  .card {
    position: relative; width: 540px; height: 309px; overflow: hidden;
    box-shadow: 0 18px 40px rgba(0,0,0,.55);
  }
  /* Information side */
  .card--info { background: var(--card-dark); color: var(--text-light); }
  .brand {
    position: absolute; display: flex; align-items: center; gap: 12px;
    font-weight: 700; white-space: nowrap;
  }
  .card--info .brand { top: 58px; left: 230px; font-size: 30px; color: var(--brand-blue); }
  .brand__mark { width: 22px; height: 22px; background: currentColor; flex: none; }
  .holder { position: absolute; left: 46px; top: 138px; text-align: right; width: 180px; }
  .holder__name {
    font-family: "Roboto Condensed", "Arial Narrow", sans-serif;
    font-weight: 700; font-size: 25px; line-height: 1.1;
  }
  .holder__first { color: var(--brand-blue); display: block; }
  .holder__last { color: var(--text-grey); display: block; }
  .holder__role { font-size: 13px; margin-top: 5px; color: var(--text-light); }
  .divider {
    position: absolute; left: 250px; top: 142px; width: 1px; height: 78px;
    background: linear-gradient(to bottom, transparent, #d9d9d9 50%, transparent);
  }
  .contacts { position: absolute; left: 270px; top: 160px; list-style: none; font-size: 14px; }
  .contacts li { display: flex; align-items: center; gap: 8px; margin-bottom: 8px; }
  .contacts svg { width: 13px; height: 13px; fill: var(--brand-blue); flex: none; }
  .address-band {
    position: absolute; left: 0; right: 0; bottom: 22px; height: 34px;
    background: var(--brand-blue); color: var(--text-light);
    display: flex; align-items: center; padding-left: 70px;
    font-size: 15px; font-weight: 500;
  }
  /* Brand side */
  .card--brand { background: var(--brand-blue); }
  .card--brand .brand {
    top: 50%; left: 50%; transform: translate(-50%, -50%);
    font-size: 40px; color: var(--ink);
  }
  .card--brand .brand__mark { width: 30px; height: 30px; }
</style>
</head>
<body>
<main class="canvas">
  <section class="card card--info" aria-label="Business card, contact side">
    <div class="brand"><span class="brand__mark"></span>RWT Fittings Ltd</div>
    <div class="holder">
      <h1 class="holder__name"><span class="holder__first">Marco</span><span class="holder__last">Peltieri</span></h1>
      <p class="holder__role">Owner &amp; Manager</p>
    </div>
    <div class="divider"></div>
    <ul class="contacts">
      <li>
        <svg viewBox="0 0 24 24" aria-hidden="true"><path d="M6.6 10.8a15 15 0 0 0 6.6 6.6l2.2-2.2c.3-.3.7-.4 1-.2 1.1.4 2.3.6 3.6.6.6 0 1 .4 1 1V20c0 .6-.4 1-1 1A17 17 0 0 1 3 4c0-.6.4-1 1-1h3.5c.6 0 1 .4 1 1 0 1.3.2 2.5.6 3.6.1.3 0 .7-.2 1z"/></svg>
        1604 551 8293
      </li>
      <li>
        <svg viewBox="0 0 24 24" aria-hidden="true"><path d="M2 5h20v14H2zm2 2v.5l8 5 8-5V7zm0 3v7h16v-7l-8 5z"/></svg>
        RWTFittings@mailbox-demo.com
      </li>
    </ul>
    <div class="address-band">1407-5194 Linden Row Burnaby BC, V5H 2K9</div>
  </section>

  <section class="card card--brand" aria-label="Business card, brand side">
    <div class="brand"><span class="brand__mark"></span>RWT Fittings Ltd</div>
  </section>
</main>
</body>
</html>
```